Naturopath Practitioner Card Design

I am a naturopath needing a design for a business card mainly to show that I am a naturopath and have some contact details to give to prospective clients. I am open minded about the design and what is on the second side of the card whether it just be some artwork or space for details, appointment times etc. Naturopathy is the practice of natural medicine that uses a holistic approach and incorporates herbal and nutritional medicine.

Industry/Entity Type

Business

Contact Information for Business Card

Tom Rudd NaturopathBHSc (Naturopathy) Member WHPG 0487 925 316 tom.rudd@mailexample.com www.tomruddnaturopathy.example.au

Requirements
Nice to have
• Would prefer some kind of original pattern/art work/logo rather than an image, not fussed if its very simple/basic
• I am open to any colour but think I would prefer a more earthy sandy clay etc type style than the greens that are commonly associated with naturopathy.
Should not have
• Don't really want to have generic stock images on it

```html
<!DOCTYPE html>
<html lang="en">
<head>
<meta charset="utf-8">
<title>Tom Rudd Naturopath – Business Card</title>
<link href="https://fonts.googleapis.com/css2?family=Open+Sans:wght@400;600;700&display=swap" rel="stylesheet">
<style>
  :root {
    --page-bg: #efece6;
    --card-white: #ffffff;
    --leaf-green: #2fa52b;
    --leaf-light: #b9e27a;
    --leaf-mid: #7cc63f;
    --leaf-deep: #3e9a1f;
    --ink: #1d1d1d;
    --dot-ink: #333333;
  }
  * { box-sizing: border-box; margin: 0; padding: 0; }
  html, body {
    width: 1200px; height: 900px; overflow: hidden;
    background: var(--page-bg);
    font-family: "Open Sans", Arial, sans-serif;
  }
  .sheet {
    width: 1200px; height: 900px;
    display: flex; flex-direction: column; align-items: center; justify-content: center;
    gap: 40px;
  }
  .card {
    position: relative;
    width: 700px; height: 400px;
    background: var(--card-white);
    overflow: hidden;
    box-shadow: 0 6px 18px rgba(0,0,0,0.18);
  }

  /* Appointment side */
  .appointment-art {
    position: absolute; top: 0; right: 0; width: 360px; height: 150px;
    background: radial-gradient(ellipse at 80% 30%, var(--leaf-light) 0%, rgba(185,226,122,0.55) 35%, rgba(255,255,255,0) 75%);
  }
  .appointment {
    position: absolute; left: 60px; top: 110px; right: 60px;
    color: var(--ink);
  }
  .appointment-title {
    color: var(--leaf-green); font-weight: 700; font-size: 24px;
  }
  .field-row {
    display: flex; align-items: flex-end; gap: 8px;
    font-weight: 700; font-size: 18px; margin-top: 30px;
  }
  .field-row.first { margin-top: 14px; }
  .dots {
    flex: 1; border-bottom: 2px dotted var(--dot-ink); height: 1px; margin-bottom: 5px;
  }
  .dots.short { flex: 0 0 150px; }
  .dots.mid { flex: 0 0 120px; }
  .ampm { font-weight: 400; font-size: 15px; }
  .spacer { width: 16px; }
  .appointment-note {
    margin-top: 30px; color: var(--leaf-green); font-weight: 700; font-size: 17px;
  }

  /* Contact side */
  .contact-art {
    position: absolute; inset: 0;
    background:
      radial-gradient(ellipse at 95% 45%, var(--leaf-deep) 0%, rgba(62,154,31,0.7) 18%, rgba(62,154,31,0) 40%),
      radial-gradient(ellipse at 12% 88%, var(--leaf-deep) 0%, rgba(62,154,31,0.6) 18%, rgba(62,154,31,0) 38%),
      linear-gradient(180deg, var(--card-white) 0%, var(--card-white) 22%, #dff0c0 42%, var(--leaf-light) 58%, var(--leaf-mid) 80%, #5fb22e 100%);
  }
  .contact {
    position: absolute; left: 340px; top: 30px; color: var(--ink);
  }
  .contact-name { color: var(--leaf-green); font-weight: 700; font-size: 32px; line-height: 1.2; }
  .contact-role { font-size: 19px; line-height: 1.3; }
  .contact-lines { margin-top: 22px; font-size: 21px; line-height: 1.35; }
  .contact-line { display: flex; align-items: center; gap: 8px; }
  .contact-line svg { width: 16px; height: 16px; flex: none; }
</style>
</head>
<body>
<main class="sheet">
  <section class="card card-appointment">
    <div class="appointment-art" role="img" aria-label="Soft photo of fresh green leaves in the top right corner"></div>
    <div class="appointment">
      <h2 class="appointment-title">Your Next Appointment on</h2>
      <div class="field-row first"><span class="dots"></span></div>
      <div class="field-row"><span>Name :</span><span class="dots"></span></div>
      <div class="field-row">
        <span>Date :</span><span class="dots short"></span><span class="spacer"></span>
        <span>Time :</span><span class="dots mid"></span><span class="ampm">AM / PM</span>
      </div>
      <p class="appointment-note">If unable to keep appointment, kindly give 24hrs notice.</p>
    </div>
  </section>

  <section class="card card-contact">
    <div class="contact-art" role="img" aria-label="Blurred green garden photo with leaves in the lower left and right corners"></div>
    <div class="contact">
      <h1 class="contact-name">Tom Rudd</h1>
      <p class="contact-role">Naturopath</p>
      <p class="contact-role">BHSc (Naturopathy) Member WHPG</p>
      <div class="contact-lines">
        <p class="contact-line">
          <svg viewBox="0 0 16 16" aria-hidden="true"><path fill="#2fa52b" d="M3.6 1.2l2.3 2.6-1.3 1.7c.9 2 2.4 3.6 4.4 4.6l1.7-1.3 2.6 2.3-1.3 2.3C7 13.1 2.8 8.9 1.3 3.1z"/></svg>
          <span>0487 925 316</span>
        </p>
        <p class="contact-line">
          <svg viewBox="0 0 16 16" aria-hidden="true"><rect x="1" y="3.5" width="14" height="9.5" fill="#2fa52b"/><path d="M1.5 4l6.5 5 6.5-5" fill="none" stroke="#fff" stroke-width="1.2"/></svg>
          <span>tom.rudd@mailexample.com</span>
        </p>
      </div>
    </div>
  </section>
</main>
</body>
</html>
```